Lanternfield Drinks business cards

We need a business card design for our new logo. The company is modern, progressive, professional, yet approachable. The key products are ready to drink bottles and cans of coffee based beverages.
These cards will be a critical part of the first impression made by our sales organization, business development team, and all external facing personnel.
Card can be a vertical or horizontal orientation.

Target Market(s)

Customers, suppliers, business partners

Industry/Entity Type

Business

Contact Information for Business Card

Business cards should feature Company Name and Logo.

Font styles to use
Serif

Colors

Designer to choose colors to be used in the design.

Requirements
Must have
• Strong readability of Name, phone #, mobile number and email address.
• Job title, website url, Street Address, and other details can be secondary level readability.
Nice to have
• High impact, simplistic quality design.
• Ok to utilize the 'H in the box' separate from the company name

```html
<!DOCTYPE html>
<html lang="en">
<head>
<meta charset="utf-8">
<title>Lanternfield Drinks – Business Cards</title>
<link href="https://fonts.googleapis.com/css2?family=Cinzel:wght@700&family=Zilla+Slab:wght@300;400&display=swap" rel="stylesheet">
<style>
  :root {
    --backdrop: #1b1b1c;
    --charcoal: #2a2425;
    --charcoal-deep: #1f1a1b;
    --orange: #f08a45;
    --orange-deep: #e4602f;
    --orange-light: #f7a35c;
    --amber: #f0b13a;
    --amber-light: #f4c04e;
    --white: #ffffff;
    --paper: #f4f2f0;
  }
  * { box-sizing: border-box; margin: 0; padding: 0; }
  html, body { width: 1200px; height: 864px; overflow: hidden; }
  body {
    background: var(--backdrop);
    display: flex;
    align-items: center;
    justify-content: center;
    gap: 40px;
    font-family: "Zilla Slab", Georgia, serif;
  }
  .card {
    position: relative;
    width: 540px;
    height: 309px;
    overflow: hidden;
    box-shadow: 0 14px 30px rgba(0,0,0,.55);
  }

  /* ---------- Front ---------- */
  .card--front { background: var(--charcoal); }
  .front__address-band {
    position: absolute; left: 0; top: 170px; width: 340px; height: 42px;
    background: linear-gradient(90deg, var(--amber), var(--amber-light));
    color: var(--white);
    font-weight: 300; font-size: 12.5px; letter-spacing: .3px;
    display: flex; align-items: center; justify-content: center;
  }
  .front__brand {
    position: absolute; left: 0; top: 96px; width: 340px;
    display: flex; align-items: center; justify-content: center; gap: 10px;
  }
  .brand-square {
    width: 30px; height: 30px; border: 2.5px solid var(--orange);
  }
  .brand-name {
    font-family: "Cinzel", Georgia, serif; font-weight: 700;
    font-size: 20px; color: var(--orange); letter-spacing: .5px;
  }
  .front__contact-panel {
    position: absolute; left: 340px; top: 0; width: 160px; height: 100%;
    background: linear-gradient(160deg, var(--orange) 0%, var(--orange-light) 100%);
    color: var(--white); text-align: right; padding: 34px 12px 0 10px;
  }
  .person-name {
    font-family: "Cinzel", Georgia, serif; font-weight: 700;
    font-size: 12.5px; letter-spacing: .3px; white-space: nowrap;
  }
  .person-title { font-size: 11.5px; font-weight: 400; margin-top: 1px; }
  .contact-list {
    list-style: none; position: absolute; right: 12px; top: 176px;
    font-size: 11.5px; font-weight: 300; line-height: 18px;
  }
  .front__icon-strip {
    position: absolute; left: 500px; top: 0; width: 40px; height: 100%;
    background: var(--charcoal-deep);
  }
  .icon-list {
    list-style: none; position: absolute; left: 12px; top: 178px;
    display: flex; flex-direction: column; gap: 5px;
  }
  .icon-list li {
    width: 13px; height: 13px; border: 1px solid var(--amber);
    display: flex; align-items: center; justify-content: center;
  }
  .icon-list svg { width: 9px; height: 9px; fill: var(--amber); }

  /* ---------- Back ---------- */
  .card--back {
    background: linear-gradient(160deg, var(--orange-light) 0%, var(--orange) 45%, var(--orange-deep) 100%);
  }
  .back__edge {
    position: absolute; left: 0; top: 0; width: 24px; height: 100%;
    background: linear-gradient(180deg, var(--amber), var(--orange-light));
  }
  .back__blank-panel {
    position: absolute; left: 24px; top: 0; width: 150px; height: 100%;
    background: linear-gradient(180deg, var(--white), var(--paper));
  }
  .back__band {
    position: absolute; left: 174px; top: 188px; width: 366px; height: 52px;
    background: linear-gradient(90deg, var(--amber), rgba(240,177,58,.55));
  }
  .back__ghost {
    position: absolute; width: 76px; height: 76px; top: 80px;
    border: 2px solid rgba(255,255,255,.12);
  }
  .back__ghost--one { left: 196px; }
  .back__ghost--two { left: 262px; border-color: rgba(255,255,255,.2); }
  .back__brand {
    position: absolute; right: 22px; top: 60px;
    display: flex; flex-direction: column; align-items: center; gap: 10px;
  }
  .back__brand .brand-square { width: 110px; height: 110px; border: 4px solid var(--white); }
  .back__brand .brand-name { color: var(--white); font-size: 15px; }
  .back__web {
    position: absolute; right: 22px; bottom: 42px;
    color: var(--white); font-size: 12px; font-weight: 400; letter-spacing: .3px;
  }
</style>
</head>
<body>

  <section class="card card--front" aria-label="Business card front">
    <div class="front__brand">
      <span class="brand-square"></span>
      <span class="brand-name">LANTERNFIELD DRINKS</span>
    </div>
    <div class="front__address-band">418 Harbor Ridge Rd, Westbrook, NY 11590</div>

    <div class="front__contact-panel">
      <p class="person-name">DANIEL WHITCOMBE</p>
      <p class="person-title">Managing Director</p>
      <ul class="contact-list">
        <li>555.014.2270</li>
        <li>555.019.3384</li>
        <li>daniel@lanternfielddrinks.com</li>
      </ul>
    </div>

    <div class="front__icon-strip">
      <ul class="icon-list">
        <li><svg viewBox="0 0 24 24" aria-label="Phone"><path d="M6.6 10.8a15.1 15.1 0 0 0 6.6 6.6l2.2-2.2c.3-.3.7-.4 1-.2 1.1.4 2.3.6 3.6.6.6 0 1 .4 1 1V20c0 .6-.4 1-1 1C10.6 21 3 13.4 3 4c0-.6.4-1 1-1h3.5c.6 0 1 .4 1 1 0 1.3.2 2.5.6 3.6.1.3 0 .7-.2 1z"/></svg></li>
        <li><svg viewBox="0 0 24 24" aria-label="Mobile"><path d="M7 2h10a2 2 0 0 1 2 2v16a2 2 0 0 1-2 2H7a2 2 0 0 1-2-2V4a2 2 0 0 1 2-2zm0 3v13h10V5zm5 14.2a1 1 0 1 0 0 .1z"/></svg></li>
        <li><svg viewBox="0 0 24 24" aria-label="Email"><path d="M3 5h18v14H3zm2 2v.4l7 4.6 7-4.6V7zm0 2.8V17h14V9.8l-7 4.6z"/></svg></li>
      </ul>
    </div>
  </section>

  <section class="card card--back" aria-label="Business card back">
    <div class="back__edge"></div>
    <div class="back__blank-panel"></div>
    <div class="back__band"></div>
    <span class="back__ghost back__ghost--one"></span>
    <span class="back__ghost back__ghost--two"></span>
    <div class="back__brand">
      <span class="brand-square"></span>
      <span class="brand-name">LANTERNFIELD DRINKS</span>
    </div>
    <p class="back__web">www.lanternfielddrinks.com</p>
  </section>

</body>
</html>
```